White Paper and One-Page Advertisement for TELVORISH-QM

I need both documents to be better formatted and designed so they look professional, not something someone with mediocre word skills put together. They will go out to 1000s of industry professionals, and they need to look sharp. I need them to have my company's color palate logo, and branding on it similar to how it is now, but better. Please do not change any of the written content, but it can be arranged in any other format you think is better. Smart art and things i've already used can be omitted in favor of better designs. The developer is free to use their creativity. White paper should not be longer than the three pages unless necessary.

Target Market(s)

Life Sciences supply chain professionals

Colors
33b8a4
0592cd
9bcb3c
fbee3e
3277b5

Requirements
Must have
• Must be professional looking and not look like something done in word. Please use the color palate as seen on the documents.
Should not have
• Any changes to the written content.

```html
<!DOCTYPE html>
<html lang="en">
<head>
<meta charset="utf-8">
<title>TELVORISH-QM – Changing Pharma's Paradigm of Waste</title>
<link href="https://fonts.googleapis.com/css2?family=Open+Sans:wght@400;600;700;800&display=swap" rel="stylesheet">
<style>
:root{
  --teal:#33b8a4;
  --blue:#0592cd;
  --blue-deep:#3277b5;
  --green:#9bcb3c;
  --yellow:#fbee3e;
  --sky:#cfe8f6;
  --sky-mid:#a8d4ee;
  --ink:#2f3338;
  --charcoal:#3b3e42;
  --grey-text:#4a4f55;
  --backdrop:#dcd9d5;
  --photo-warm:#b9aea4;
  --photo-cool:#8fa6b8;
}
*{box-sizing:border-box;margin:0;padding:0}
html,body{width:1200px;height:2368px;overflow:hidden}
body{background:var(--backdrop);font-family:"Open Sans",Arial,sans-serif;color:var(--ink);position:relative}

.page{position:absolute;width:560px;height:725px;background:#fff;overflow:hidden;box-shadow:0 2px 8px rgba(0,0,0,.12)}
.page > svg.page-art{position:absolute;left:0;top:0;width:560px;height:725px}
.row-cover .page{left:320px;top:48px}
.row-outer .back{left:40px;top:821px}
.row-outer .front{left:600px;top:821px}
.row-inner .left{left:40px;top:1594px}
.row-inner .right{left:600px;top:1594px}

/* brand */
.brand{position:absolute;left:28px;top:48px;display:flex;align-items:center;gap:6px}
.brand-dot{width:18px;height:18px;border-radius:50%;background:var(--green)}
.brand-name{font-weight:800;font-size:13px;color:var(--teal);letter-spacing:.3px}

.cover-title{position:absolute;left:28px;top:74px;width:280px;font-weight:800;font-size:21px;line-height:22px;color:var(--ink);text-transform:uppercase}
.cover-sub{position:absolute;left:110px;top:178px;width:420px;text-align:center;font-weight:800;font-size:16px;line-height:19px;color:var(--blue-deep)}
.cover-sub .byline{display:block;color:var(--ink);font-size:17px;margin-top:2px}

.tab{position:absolute;height:20px;padding:0 22px 0 12px;background:var(--blue);color:#fff;font-weight:700;font-size:12px;line-height:20px;clip-path:polygon(0 0,88% 0,100% 100%,0 100%)}
.copy{position:absolute;font-size:7.6px;line-height:10.4px;color:var(--grey-text);text-align:justify}
.copy p{margin-bottom:6px}
.copy strong{color:var(--ink)}

.cover-overview{left:28px;top:272px}
.cover-copy{left:28px;top:296px;width:504px;font-weight:600;font-size:8px;line-height:11px;color:var(--ink)}

.contact{position:absolute;display:flex;align-items:center;gap:6px;font-size:8.5px;color:#fff}
.contact svg{width:14px;height:14px}

/* back page */
.bullets{position:absolute;list-style:none;font-size:7.6px;line-height:10.4px;color:var(--grey-text)}
.bullets li{position:relative;padding-left:10px}
.bullets li::before{content:"";position:absolute;left:0;top:3.5px;width:4px;height:4px;background:var(--blue)}
.platform-list{left:22px;top:114px;width:340px}
.benefit-list{left:22px;top:250px;width:340px}
.photo-stack{position:absolute;left:382px;top:22px;width:156px}
.photo{border:3px solid #fff;box-shadow:0 0 0 1px var(--sky-mid)}
.photo-stack .photo{height:98px;margin-bottom:8px}
.p1{background:linear-gradient(160deg,#8a6f5c,#c9b3a0)}
.p2{background:linear-gradient(160deg,#2e5fa8,#c7c2bd)}
.p3{background:linear-gradient(160deg,#c9c0b8,#8e8a86)}

.stats{position:absolute;left:22px;top:338px;display:flex;gap:8px}
.stat{width:82px}
.stat-fig{height:22px;color:#fff;font-weight:800;font-size:13px;line-height:22px;text-align:center}
.stat-label{height:60px;padding:5px 6px;color:#fff;font-weight:700;font-size:8px;line-height:10px}
.stat.green .stat-fig{background:var(--green)}
.stat.green .stat-label{background:#86b52f}
.stat.lime .stat-fig{background:#b8d86a}
.stat.lime .stat-label{background:var(--green)}
.stat.sea .stat-fig{background:var(--teal)}
.stat.sea .stat-label{background:#2a9d8b}
.stat.azure .stat-fig{background:var(--blue)}
.stat.azure .stat-label{background:var(--blue-deep)}

.team-photo{position:absolute;left:0;top:440px;width:560px;height:285px;background:linear-gradient(170deg,#6c5d4e,#b59b7c 55%,#4c4a48)}

/* inner */
.numbers-tab{left:22px;top:70px}
.numbers-copy{left:22px;top:98px;width:516px}
.more-tab{left:22px;top:70px}
.more-col{position:absolute;top:98px;width:250px;font-size:7.4px;line-height:10px;color:var(--grey-text)}
.more-col p{margin-bottom:7px}
.more-col.a{left:22px}
.more-col.b{left:290px}
</style>
</head>
<body>

<!-- Row 1: front cover -->
<section class="row-cover">
  <article class="page cover">
    <svg class="page-art" viewBox="0 0 560 725" aria-hidden="false">
      <defs>
        <linearGradient id="bodyGrad1" x1="0" y1="0" x2="0" y2="1">
          <stop offset="0" stop-color="#ffffff"/><stop offset=".35" stop-color="#e6f3fb"/><stop offset="1" stop-color="#bfe0f3"/>
        </linearGradient>
        <linearGradient id="babyGrad1" x1="0" y1="0" x2="1" y2="1">
          <stop offset="0" stop-color="#a89a8c"/><stop offset=".5" stop-color="#d8ccc1"/><stop offset="1" stop-color="#9c8e82"/>
        </linearGradient>
      </defs>
      <rect x="0" y="0" width="560" height="725" fill="url(#bodyGrad1)"/>
      <path role="img" aria-label="Photo of a baby in a knitted hood" fill="url(#babyGrad1)" d="M250 0H560V150C470 128 400 150 340 170C300 140 270 90 250 0Z"/>
      <path d="M230 140C300 175 360 160 440 140C490 128 530 130 560 138V152C520 144 480 146 440 156C360 176 300 190 230 150Z" fill="var(--sky-mid)"/>
      <path d="M0 430C90 440 180 470 230 500L200 470L290 440C200 428 90 420 0 418Z" fill="var(--sky-mid)" opacity=".8"/>
      <path d="M0 560C120 540 230 600 330 585C420 572 490 560 560 540V725H0Z" fill="var(--sky-mid)"/>
      <path d="M0 600C140 585 250 640 360 622C450 608 510 598 560 590V725H0Z" fill="var(--blue)" opacity=".55"/>
      <path d="M0 640C150 630 280 660 380 648C460 638 520 630 560 628V725H0Z" fill="var(--charcoal)"/>
    </svg>
    <div class="brand"><span class="brand-dot"></span><span class="brand-name">TELVORISH-QM</span></div>
    <h1 class="cover-title">Changing Pharma's Paradigm of Waste</h1>
    <h2 class="cover-sub">How Pharma's Demand Volatility Could Be Costing You Millions in Material Write-downs &amp; Procurement<span class="byline">Dale Marston &nbsp;|&nbsp; August 2018</span></h2>
    <div class="tab cover-overview">Overview</div>
    <div class="copy cover-copy">Demand volatility is a challenge for every supply chain. It strikes at the end of supply chains causing a "bull-whip effect" that becomes exponentially more impactful further back in the chain. For Pharma, the effect is strongest in manufacturing and procurement, specifically with starting raw materials and consumables. Swings in demand can cripple launches, cause stock-outs, inflate material prices, make lean planning ineffective, and cause significant write-downs of residual and obsolete materials, ultimately inflating CoGS and reducing net income. These swings can also cause inventory costs to inflate, materials to expire or become obsolete, higher disposal fees, and a larger carbon footprint. The yearly financial impacts are staggering considering Pharma's economic footprint. Twenty of Pharma's top 100 companies were sampled using 2015 &amp; 2016 financial figures 1-2-3-4. Industry estimates for waste include:</div>
    <div class="contact" style="left:250px;top:658px"><svg viewBox="0 0 14 14"><circle cx="7" cy="7" r="7" fill="#fff"/><rect x="3.5" y="4.5" width="7" height="5" fill="none" stroke="#3b3e42" stroke-width="1"/><path d="M3.5 4.5L7 7.5L10.5 4.5" fill="none" stroke="#3b3e42" stroke-width="1"/></svg>info@telvorishqm.com</div>
    <div class="contact" style="left:430px;top:658px"><svg viewBox="0 0 14 14"><circle cx="7" cy="7" r="7" fill="#fff"/><path d="M4.5 3.5L6 3.5L6.8 5.6L5.8 6.3C6.3 7.4 6.9 8 8 8.5L8.7 7.5L10.5 8.3V9.8C7 10 4.2 7 4.5 3.5Z" fill="#3b3e42"/></svg>844-555-TVQM</div>
    <div class="contact" style="left:28px;top:696px"><svg viewBox="0 0 14 14"><circle cx="7" cy="7" r="7" fill="#fff"/><circle cx="7" cy="7" r="3.6" fill="none" stroke="#3b3e42" stroke-width="1"/><path d="M3.4 7H10.6M7 3.4V10.6" stroke="#3b3e42" stroke-width=".8"/></svg>www.telvorishqm.com</div>
  </article>
</section>

<!-- Row 2: back cover + front cover -->
<section class="row-outer">
  <article class="page back">
    <svg class="page-art" viewBox="0 0 560 725">
      <defs>
        <linearGradient id="bodyGrad2" x1="0" y1="0" x2="0" y2="1">
          <stop offset="0" stop-color="#ffffff"/><stop offset="1" stop-color="#d7ebf7"/>
        </linearGradient>
      </defs>
      <rect width="560" height="725" fill="url(#bodyGrad2)"/>
      <path d="M0 0H560V18C420 30 260 40 0 30Z" fill="var(--sky-mid)" opacity=".6"/>
    </svg>
    <div class="tab" style="left:22px;top:90px">Our Platform</div>
    <ul class="bullets platform-list">
      <li>A single online marketplace built for the life science community.</li>
      <li>Buyers, manufacturers and original suppliers can list surplus raw materials and after-market stock.</li>
      <li>Researchers, labs and distributors gain access to verified material at fair value.</li>
      <li>Part 11 compliant tracking, audit trail and authentication.</li>
      <li>Leverages industry-leading data to match supply with demand.</li>
      <li>Built for compliance, traceability and accountability.</li>
      <li>Serves life science and industry vendors and software teams.</li>
    </ul>
    <div class="tab" style="left:22px;top:226px">Benefits</div>
    <ul class="bullets benefit-list">
      <li>Reduce write-offs by selling excess and obsolete materials.</li>
      <li>Lower disposal fees, storage and carrying costs.</li>
      <li>Buy quality materials at a reduced price.</li>
      <li>Recover value from an original supplier.</li>
      <li>Donate material to researchers in need.</li>
      <li>Collaborate and connect to reduce supply chain risk and shrink your carbon footprint.</li>
    </ul>
    <div class="photo-stack">
      <div class="photo p1" role="img" aria-label="Photo of a smiling lab researcher"></div>
      <div class="photo p2" role="img" aria-label="Photo of a senior patient"></div>
      <div class="photo p3" role="img" aria-label="Photo of a baby"></div>
    </div>
    <div class="stats">
      <div class="stat green"><div class="stat-fig">4.7%</div><div class="stat-label">Avg Raw Material Write-down as a % of Net Income</div></div>
      <div class="stat lime"><div class="stat-fig">$2.7B</div><div class="stat-label">Est Pharma Written Down Inventory in 2016</div></div>
      <div class="stat sea"><div class="stat-fig">$2,034</div><div class="stat-label">Est's Pharma Expense per $1B Net MSW Waste</div></div>
      <div class="stat azure"><div class="stat-fig">.01</div><div class="stat-label">Carbon Footprint of Material Writedown and Firm Size</div></div>
    </div>
    <div class="team-photo" role="img" aria-label="Photo of a team reviewing samples together"></div>
    <svg class="page-art" viewBox="0 0 560 725" style="pointer-events:none">
      <path d="M0 440C140 420 300 460 560 430V470C300 490 150 450 0 470Z" fill="#fff"/>
    </svg>
  </article>

  <article class="page front">
    <svg class="page-art" viewBox="0 0 560 725">
      <defs>
        <linearGradient id="bodyGrad3" x1="0" y1="0" x2="0" y2="1">
          <stop offset="0" stop-color="#ffffff"/><stop offset=".35" stop-color="#e6f3fb"/><stop offset="1" stop-color="#bfe0f3"/>
        </linearGradient>
        <linearGradient id="babyGrad3" x1="0" y1="0" x2="1" y2="1">
          <stop offset="0" stop-color="#a89a8c"/><stop offset=".5" stop-color="#d8ccc1"/><stop offset="1" stop-color="#9c8e82"/>
        </linearGradient>
      </defs>
      <rect width="560" height="725" fill="url(#bodyGrad3)"/>
      <path role="img" aria-label="Photo of a baby in a knitted hood" fill="url(#babyGrad3)" d="M250 0H560V150C470 128 400 150 340 170C300 140 270 90 250 0Z"/>
      <path d="M230 140C300 175 360 160 440 140C490 128 530 130 560 138V152C520 144 480 146 440 156C360 176 300 190 230 150Z" fill="var(--sky-mid)"/>
      <path d="M0 430C90 440 180 470 230 500L200 470L290 440C200 428 90 420 0 418Z" fill="var(--sky-mid)" opacity=".8"/>
      <path d="M0 560C120 540 230 600 330 585C420 572 490 560 560 540V725H0Z" fill="var(--sky-mid)"/>
      <path d="M0 600C140 585 250 640 360 622C450 608 510 598 560 590V725H0Z" fill="var(--blue)" opacity=".55"/>
      <path d="M0 640C150 630 280 660 380 648C460 638 520 630 560 628V725H0Z" fill="var(--charcoal)"/>
    </svg>
    <div class="brand"><span class="brand-dot"></span><span class="brand-name">TELVORISH-QM</span></div>
    <h1 class="cover-title">Changing Pharma's Paradigm of Waste</h1>
    <h2 class="cover-sub">How Pharma's Demand Volatility Could Be Costing You Millions in Material Write-downs &amp; Procurement<span class="byline">Dale Marston &nbsp;|&nbsp; August 2018</span></h2>
    <div class="tab cover-overview">Overview</div>
    <div class="copy cover-copy">Demand volatility is a challenge for every supply chain. It strikes at the end of supply chains causing a "bull-whip effect" that becomes exponentially more impactful further back in the chain. For Pharma, the effect is strongest in manufacturing and procurement, specifically with starting raw materials and consumables. Swings in demand can cripple launches, cause stock-outs, inflate material prices, make lean planning ineffective, and cause significant write-downs of residual and obsolete materials, ultimately inflating CoGS and reducing net income. These swings can also cause inventory costs to inflate, materials to expire or become obsolete, higher disposal fees, and a larger carbon footprint. The yearly financial impacts are staggering considering Pharma's economic footprint. Twenty of Pharma's top 100 companies were sampled using 2015 &amp; 2016 financial figures 1-2-3-4. Industry estimates for waste include:</div>
    <div class="contact" style="left:250px;top:658px"><svg viewBox="0 0 14 14"><circle cx="7" cy="7" r="7" fill="#fff"/><rect x="3.5" y="4.5" width="7" height="5" fill="none" stroke="#3b3e42" stroke-width="1"/><path d="M3.5 4.5L7 7.5L10.5 4.5" fill="none" stroke="#3b3e42" stroke-width="1"/></svg>info@telvorishqm.com</div>
    <div class="contact" style="left:430px;top:658px"><svg viewBox="0 0 14 14"><circle cx="7" cy="7" r="7" fill="#fff"/><path d="M4.5 3.5L6 3.5L6.8 5.6L5.8 6.3C6.3 7.4 6.9 8 8 8.5L8.7 7.5L10.5 8.3V9.8C7 10 4.2 7 4.5 3.5Z" fill="#3b3e42"/></svg>844-555-TVQM</div>
    <div class="contact" style="left:28px;top:696px"><svg viewBox="0 0 14 14"><circle cx="7" cy="7" r="7" fill="#fff"/><circle cx="7" cy="7" r="3.6" fill="none" stroke="#3b3e42" stroke-width="1"/><path d="M3.4 7H10.6M7 3.4V10.6" stroke="#3b3e42" stroke-width=".8"/></svg>www.telvorishqm.com</div>
  </article>
</section>

<!-- Row 3: inner spread -->
<section class="row-inner">
  <article class="page left">
    <svg class="page-art" viewBox="0 0 560 725">
      <defs>
        <linearGradient id="innerGrad1" x1="0" y1="0" x2="0" y2="1">
          <stop offset="0" stop-color="#ffffff"/><stop offset="1" stop-color="#e3f1fa"/>
        </linearGradient>
      </defs>
      <rect width="560" height="725" fill="url(#innerGrad1)"/>
      <path d="M0 0H560V20C400 60 200 40 0 62Z" fill="var(--sky-mid)"/>
      <path d="M0 0H560V8C400 40 200 26 0 44Z" fill="var(--blue)" opacity=".6"/>
      <path d="M0 640C150 620 300 660 560 630V725H0Z" fill="var(--sky-mid)"/>
      <path d="M0 670C160 656 320 690 560 664V725H0Z" fill="var(--charcoal)"/>
    </svg>
    <div class="tab numbers-tab">What Do These Numbers Mean?</div>
    <div class="copy numbers-copy">
      <p><strong>4.7% is an alarmingly high figure</strong> and does not include capitalized consumables, equipment disposal, and general material waste. Considering how much net income is lost to write-downs each year, even a small reduction would return significant value to shareholders and to the programs that depend on them.</p>
      <p>$2.7B of inventory written down by the sampled companies alone suggests the industry-wide figure is far higher. Much of this material is still usable, within expiry, and of value to other manufacturers, researchers and laboratories who would gladly purchase it at a fair price.</p>
      <p>Disposal is costly as well. Many companies pay specialized vendors to incinerate or landfill residual materials, adding transport, handling and documentation costs. These fees rise each year and do nothing to recover the original investment made in the material.</p>
      <p>Companies have attempted to manage the problem internally through better forecasting, safety stock adjustments and vendor-managed inventory. While these tools help, they cannot remove volatility at its source. Launch timing, regulatory changes, market shifts and clinical outcomes will always create swings in demand that planners cannot predict.</p>
      <p>A life science-specific exchange platform offers another path. By connecting companies holding excess material with those who need it, value can be recovered rather than destroyed, procurement costs can fall, and lead times for buyers can shrink considerably.</p>
      <p>It is a call to arms across supply chains. Collaboration between manufacturers, suppliers, distributors and research organizations is the most practical way to reduce waste at scale. The technology now exists to make this exchange secure, compliant and simple.</p>
      <p>Let's explore Corporate Social Responsibility. Reducing material waste directly lowers the carbon footprint of each firm, supports sustainability goals and demonstrates a commitment to responsible operations. Investors and partners increasingly expect this kind of measurable progress.</p>
      <p>Reduced procurement spend is another clear outcome. Buyers who source quality surplus materials from trusted sellers can save substantially on list price while maintaining documentation and chain of custody requirements.</p>
      <p>Overall, the numbers point to a large and mostly untapped opportunity. With the right marketplace, Pharma can turn a recurring loss into recovered value, reduced waste and stronger relationships across the entire life science supply chain.</p>
      <p><strong>Contemporary Operating Environment</strong></p>
    </div>
  </article>

  <article class="page right">
    <svg class="page-art" viewBox="0 0 560 725">
      <defs>
        <linearGradient id="innerGrad2" x1="0" y1="0" x2="0" y2="1">
          <stop offset="0" stop-color="#ffffff"/><stop offset="1" stop-color="#e3f1fa"/>
        </linearGradient>
      </defs>
      <rect width="560" height="725" fill="url(#innerGrad2)"/>
      <path d="M0 0H560V62C360 40 160 60 0 20Z" fill="var(--sky-mid)"/>
      <path d="M0 0H560V44C360 26 160 40 0 8Z" fill="var(--blue)" opacity=".6"/>
      <path d="M0 630C240 660 410 620 560 640V725H0Z" fill="var(--sky-mid)"/>
      <path d="M0 664C240 690 400 656 560 670V725H0Z" fill="var(--charcoal)"/>
    </svg>
    <div class="tab more-tab">How to Find Out More</div>
    <div class="more-col a">
      <p>The exciting new marketplace called TELVORISH-QM is scheduled for initial launch this November.</p>
      <p>For more information:<br>Dale Marston<br>info@telvorishqm.com<br>Call 844-555-TVQM</p>
      <p>"We enable a greener, more cost-efficient, and quality-driven supply chain through a collaborative life science marketplace."</p>
      <p>"We are an emerging small business with the ultimate goal to reduce, reuse, and repurpose material waste, improving the bottom line for every partner."</p>
      <p>"We want to increase access to quality materials around the world and lower barriers for smaller labs."</p>
      <p>Sources:<br>1. Top 100 Pharma Companies, Industry Review 2017</p>
      <p>2. Annual Report Summaries, 2015 &amp; 2016 Financial Filings</p>
      <p>3. Total Pharma Revenue Overview, Market Data Series</p>
      <p>4. Currency Exchange Rates, Year-End Averages 2016</p>
    </div>
    <div class="more-col b">
      <p>5. Municipal Solid Waste Disposal Costs, Regional Cost Survey 2016</p>
      <p>6. Carbon Emissions from Landfill and Incineration, Environmental Review</p>
      <p>7. Inventory Write-down Practices in Life Sciences, Supply Chain Quarterly</p>
      <p>8. Demand Volatility and the Bull-whip Effect, Operations Journal</p>
      <p>9. Pricing Pressures in Raw Material Procurement, Industry Brief</p>
      <p>10. Sustainability Reporting in Pharma, Annual Benchmark Study</p>
      <p>11. Corporate Social Responsibility Trends, Global Survey 2017</p>
      <p>12. Lean Planning in Regulated Manufacturing, Practitioner Guide</p>
    </div>
  </article>
</section>

</body>
</html>
```